TLK Electricial Contracting Services

Hi guys, after a design for my small electrical company, have logo design files to be incorporated into the layout, the basic concept is electrical contracting services for residential, commercial, industrial & data services, image is clean clear and strong,

Card format is to have a nice clean logo on front,with maybe the Residential – commercial – industrial - data, followed with licensed & insured, followed by contact details on backside of the card.

Target Market(s)

Residential, commercial, industrial sectors.

Industry/Entity Type

Electrical

Contact Information for Business Card

TLK logo,
Residential – commercial – industrial - data
REC: 61307
Email: tlk@vornamail.net.au
Phone: 0487 352 019

Requirements
Must have
• Clean & strong design.
Nice to have
• If possible, I would like the logo colours inverted so the text is orange and the background is black on the front of the card, then the backside of the card be the reverse colour
Should not have
• No Sparks, lightning bolts,

```html
<!DOCTYPE html>
<html lang="en">
<head>
<meta charset="utf-8">
<title>TLK Electricial Contracting Services – Business Card</title>
<link href="https://fonts.googleapis.com/css2?family=Open+Sans:wght@400;600;700&display=swap" rel="stylesheet">
<style>
  :root {
    --stage: #3a3330;
    --card-black: #161616;
    --card-black-soft: #1e1e1e;
    --orange: #f58220;
    --white: #ffffff;
    --text-grey: #b9b9b9;
    --title-grey: #8a8a8a;
    --ghost: rgba(255,255,255,0.035);
  }
  * { margin: 0; padding: 0; box-sizing: border-box; }
  html, body { width: 1200px; height: 844px; overflow: hidden; }
  body {
    background: var(--stage);
    font-family: "Open Sans", Arial, sans-serif;
    position: relative;
  }
  .card {
    position: absolute;
    top: 273px;
    width: 520px;
    height: 298px;
    overflow: hidden;
    background: linear-gradient(135deg, var(--card-black-soft), var(--card-black));
  }

  /* ---------- Contact side ---------- */
  .card-back { left: 50px; }
  .band { position: absolute; left: 0; width: 100%; }
  .band-orange { height: 16px; background: var(--orange); }
  .band-white { height: 6px; background: var(--white); }
  .band-top.band-orange { top: 0; }
  .band-top.band-white { top: 22px; }
  .band-bottom.band-white { bottom: 22px; }
  .band-bottom.band-orange { bottom: 0; }

  .ghost-mark {
    position: absolute;
    left: 20px;
    top: 40px;
    font-weight: 700;
    font-size: 230px;
    line-height: 1;
    color: var(--ghost);
    letter-spacing: -6px;
  }
  .person {
    position: absolute;
    left: 170px;
    top: 56px;
    width: 190px;
  }
  .person-name {
    color: var(--white);
    font-size: 17px;
    font-weight: 400;
    letter-spacing: 0.5px;
    padding-bottom: 3px;
    border-bottom: 1.5px solid var(--orange);
  }
  .person-title {
    color: var(--title-grey);
    font-size: 13px;
    padding-top: 2px;
  }
  .contact-list {
    position: absolute;
    left: 0;
    right: 60px;
    top: 118px;
    list-style: none;
    text-align: center;
    color: var(--text-grey);
    font-size: 13.5px;
    line-height: 20px;
  }
  .contact-list .licence { color: var(--orange); font-weight: 600; }
  .contact-list .address { padding-left: 40px; }

  /* ---------- Logo side ---------- */
  .card-front { left: 630px; }
  .edge-tab {
    position: absolute;
    width: 22px;
    height: 40px;
    display: flex;
  }
  .edge-tab span { display: block; height: 100%; }
  .edge-tab .tab-orange { width: 14px; background: var(--orange); }
  .edge-tab .tab-white { width: 5px; background: var(--white); margin: 0 3px; }
  .edge-tab-right { right: 0; top: 40px; flex-direction: row-reverse; }
  .edge-tab-left { left: 0; top: 190px; }

  .brand {
    position: absolute;
    left: 0; right: 0;
    top: 46px;
    text-align: center;
    color: var(--orange);
    font-weight: 700;
  }
  .brand-mark {
    display: inline-flex;
    align-items: center;
    gap: 14px;
    font-size: 92px;
    line-height: 1;
    letter-spacing: -2px;
  }
  .brand-square {
    width: 22px; height: 22px;
    background: var(--orange);
  }
  .brand-name {
    margin-top: 6px;
    font-size: 20px;
    letter-spacing: 0.3px;
  }
  .brand-sectors {
    margin-top: 16px;
    color: var(--white);
    font-size: 12px;
    font-weight: 400;
    letter-spacing: 1.5px;
    text-transform: uppercase;
  }
  .brand-licensed {
    margin-top: 6px;
    color: var(--text-grey);
    font-size: 12px;
    font-weight: 400;
    letter-spacing: 1.5px;
    text-transform: uppercase;
  }
</style>
</head>
<body>

  <section class="card card-back" aria-label="Business card contact side">
    <div class="band band-orange band-top"></div>
    <div class="band band-white band-top"></div>
    <div class="ghost-mark" aria-hidden="true">TLK</div>

    <div class="person">
      <h1 class="person-name">MARCUS HALE</h1>
      <p class="person-title">Managing Director</p>
    </div>

    <ul class="contact-list">
      <li>0487 352 019</li>
      <li>08 9461 3307</li>
      <li>tlk@vornamail.net.au</li>
      <li>www.tlkelectrical.net.au</li>
      <li class="address">18 Corliss Way | Perth, WA | 6107</li>
      <li class="licence">REC: 61307</li>
    </ul>

    <div class="band band-white band-bottom"></div>
    <div class="band band-orange band-bottom"></div>
  </section>

  <section class="card card-front" aria-label="Business card logo side">
    <div class="edge-tab edge-tab-right"><span class="tab-orange"></span><span class="tab-white"></span></div>
    <div class="edge-tab edge-tab-left"><span class="tab-orange"></span><span class="tab-white"></span></div>

    <div class="brand">
      <div class="brand-mark"><span class="brand-square"></span>TLK</div>
      <div class="brand-name">Tate Lindqvist Electrical</div>
      <p class="brand-sectors">Residential – Commercial – Industrial – Data</p>
      <p class="brand-licensed">Licensed &amp; Insured</p>
    </div>
  </section>

</body>
</html>
```